Business Card Design for Flood Rescue 360 - Property Restoration Professionals

I need a business card designed for Flood Rescue 360. We are a full-service property restoration solution. Providing water, fire, smoke & storm restoration as well as mold remediation and full remodel or reconstruction to homes and businesses across Dallas-Fort Worth, TX.
Target Market(s)
home and business owners with insurance covered property damage from water, fire or storm related damage
Industry/Entity Type
property restoration
Contact Information for Business Card
Marcus Pelley General Manager Cell: 214-555-0193 Office: 469-555-0148 email: Marcus@FloodRescue360.example services: Water, Fire, Mold, Reconstruction Tagline: Urgency for Your Water Emergency!
Look and feel
Each slider illustrates characteristics of the customer's brand and the style your logo design should communicate.

```html
<!DOCTYPE html>
<html lang="en">
<head>
<meta charset="utf-8">
<title>Flood Rescue 360 – Business Card</title>
<link rel="stylesheet" href="https://fonts.googleapis.com/css2?family=Montserrat:wght@400;500;700;800&display=swap">
<style>
  :root {
    --bg: #1c1c1c;
    --card-light: #f4f4f4;
    --card-dark: #262626;
    --brand-blue: #12ace0;
    --brand-gray: #7a7a7a;
    --ink: #2a2a2a;
    --divider: #9a9a9a;
    --on-dark: #f2f2f2;
  }
  * { box-sizing: border-box; margin: 0; padding: 0; }
  html, body { width: 1200px; height: 1059px; overflow: hidden; }
  body { background: var(--bg); font-family: "Montserrat", sans-serif; position: relative; }

  .card {
    position: absolute; left: 255px; width: 690px; height: 392px;
    border-radius: 14px; overflow: hidden;
  }
  .card--front { top: 89px; background: var(--card-light); }
  .card--back { top: 547px; background: var(--card-dark); }

  .brand { position: absolute; display: flex; align-items: center; }
  .brand__name {
    font-weight: 800; color: var(--brand-blue); line-height: 0.95;
    text-transform: uppercase; letter-spacing: -0.5px;
  }
  .brand__dot { border-radius: 50%; background: var(--brand-gray); flex: none; }

  .card--front .brand { left: 36px; top: 150px; gap: 14px; }
  .card--front .brand__name { font-size: 34px; }
  .card--front .brand__dot { width: 62px; height: 62px; }

  .divider {
    position: absolute; left: 322px; top: 111px; width: 1px; height: 168px;
    background: var(--divider);
  }
  .person { position: absolute; left: 349px; top: 106px; }
  .person__name { font-size: 26px; font-weight: 700; color: var(--brand-blue); letter-spacing: 0.5px; line-height: 1; }
  .person__title { font-size: 16.5px; color: var(--ink); margin-top: 4px; letter-spacing: 0.3px; }

  .contacts { position: absolute; left: 349px; top: 178px; list-style: none; }
  .contacts li {
    display: flex; align-items: center; height: 28px;
    font-size: 16.5px; color: var(--ink); letter-spacing: 0.4px;
  }
  .contacts svg { width: 12px; height: 12px; margin-right: 7px; fill: var(--brand-blue); flex: none; }

  .band { position: absolute; left: 0; bottom: 0; width: 100%; height: 16px; }

  .card--back .brand { left: 0; right: 0; top: 112px; justify-content: center; gap: 22px; }
  .card--back .brand__name { font-size: 58px; }
  .card--back .brand__dot { width: 116px; height: 116px; }

  .services, .tagline {
    position: absolute; left: 0; right: 0; text-align: center;
    font-size: 16.5px; color: var(--on-dark); letter-spacing: 0.4px;
  }
  .services { top: 316px; }
  .services .sep { color: var(--brand-blue); margin: 0 6px; }
  .tagline { top: 345px; }
</style>
</head>
<body>
  <section class="card card--front">
    <div class="brand">
      <span class="brand__name">Flood<br>Rescue 360</span>
      <span class="brand__dot"></span>
    </div>
    <div class="divider"></div>
    <div class="person">
      <p class="person__name">MARCUS PELLEY</p>
      <p class="person__title">General Manager</p>
    </div>
    <ul class="contacts">
      <li><svg viewBox="0 0 12 12"><path d="M1 4.5C1 3 2.5 2 6 2s5 1 5 2.5L9 5 8.5 4h-5L3 5zM3 6h6l1.5 4h-9z"/></svg>469-555-0148</li>
      <li><svg viewBox="0 0 12 12"><path d="M3.5 0.5h5a1 1 0 0 1 1 1v9a1 1 0 0 1-1 1h-5a1 1 0 0 1-1-1v-9a1 1 0 0 1 1-1zM4 2v7h4V2z"/></svg>214-555-0193</li>
      <li><svg viewBox="0 0 12 12"><path d="M1 5l5-4 5 4v6H1zM2 5.5l4 3 4-3-4-3z"/></svg>Marcus@FloodRescue360.example</li>
      <li><svg viewBox="0 0 12 12"><circle cx="6" cy="6" r="5.5"/></svg>www.FloodRescue360.example</li>
    </ul>
    <svg class="band" viewBox="0 0 690 16" preserveAspectRatio="none">
      <rect x="0" y="0" width="690" height="16" fill="var(--brand-gray)"/>
      <polygon points="0,0 545,0 517,16 0,16" fill="var(--brand-blue)"/>
      <polygon points="545,0 556,0 528,16 517,16" fill="#ffffff"/>
    </svg>
  </section>

  <section class="card card--back">
    <div class="brand">
      <span class="brand__name">Flood<br>Rescue 360</span>
      <span class="brand__dot"></span>
    </div>
    <p class="services">Water<span class="sep">•</span>Fire<span class="sep">•</span>Mold<span class="sep">•</span>Reconstruction</p>
    <p class="tagline">Urgency for Your Water Emergency!</p>
  </section>
</body>
</html>
```